Tarvolen - Tarvolen Border Flow Reshaping Trade

Web Design for international start-up, which is automating customs clearance processes for forwarding companies by applying a web application, which is operating with artificial intelligence and robotic process automation. Tarvolen pursues the vision of supporting forwarding companies successfully in becoming digital masters and co-creates innovative software solutions with all participants (ex- and importers of goods) along value-added chains. With intelligent/smart/digital customs clearance software or in other words, a virtual customs clearance roboter tailord to the customers needs, we are transforming businesses. The website could look like this:

https://www.plomix.com/uk-en/index.php
or
https://sitebrenna.com/theme/halvering

Please use colours and designs you think would be the best fit. These websites are just here to give you an idea of how the webdesign could look like. Use the attached logo design as a basis for further web design. You can use the provided pictures, but you can also use your own ones, if you think they are better suited. But please take care, that they have a high resolution quality.

Description of Website: The website is transparent and modern. It provides seven pages such as homepage, products, web app, the about us, working at Tarvolen, News, contact us and search results page. The homepage or landing page should be filled with a short description of the company, what Tarvolen is doing, how they will support its customers and will also include a video of the provided solution. Products provide obviously information about different products and their characteristics. Web app page includes information about principles and technologies that get the software going. The about us page includes unique advantages and value propositions for customers and the contact us, as the name already says, will provide contact information and possibilities to contact us. The rest is also obvious (for additional information look up the website of PLX, priorly provided link - the page is also available in english).

If you have any questions, I am happy to answer them any time.
Updates

I have to think about the text that I want to have included into the design and hadn't have the time to compose it.

Target Market(s)

Forwarding Companies, Ex-/Importers

Industry/Entity Type

It Company

Number of Pages Required

5+ page

Requirements
Must have
• The web design should be designes according to the attached logo of Tarvolen.

```html
<!DOCTYPE html>
<html lang="en">
<head>
<meta charset="utf-8">
<title>Tarvolen – Border Flow Reshaping Trade</title>
<link rel="stylesheet" href="https://fonts.googleapis.com/css2?family=Lato:wght@400;700&family=Ubuntu:wght@500;700&display=swap">
<style>
:root{
  --navy:#3b48a0;
  --navy-deep:#2f3c8f;
  --cyan:#27bde0;
  --sky:#2aa8dc;
  --blue:#2e6fc0;
  --text:#4d4d55;
  --muted:#6c6c74;
  --white:#ffffff;
}
*{box-sizing:border-box;margin:0;padding:0}
html,body{width:1200px;height:3020px;overflow:hidden;background:#fff}
body{font-family:"Lato",sans-serif;color:var(--text);position:relative}
h1,h2,h3,.brand-name{font-family:"Ubuntu",sans-serif}
section,header,footer{position:absolute;left:0;width:1200px}

/* header */
.site-header{top:0;height:110px;background:#fff}
.brand{position:absolute;left:74px;top:26px;display:flex;align-items:center;gap:10px}
.brand-mark{width:32px;height:32px;background:var(--sky)}
.brand-name{font-size:40px;font-weight:500;color:var(--navy);line-height:44px}
.brand-tag{position:absolute;left:183px;top:76px;font-size:13px;line-height:16px;color:var(--navy);white-space:nowrap}
.main-nav{position:absolute;left:399px;top:49px;display:flex;gap:29px;font-size:15.5px;font-weight:700;color:#333}
.main-nav .active{color:var(--sky)}
.search{position:absolute;left:1110px;top:51px}

/* hero */
.hero{top:110px;height:549px;background:radial-gradient(ellipse at 50% 58%,#a9c6ea 0%,#3f7ccc 22%,#123c86 55%,#06193f 100%)}
.hero h1{position:absolute;top:180px;width:100%;text-align:center;font-size:92px;font-weight:700;color:#fff;letter-spacing:1px}
.hero .sub{position:absolute;top:296px;width:100%;text-align:center;font-family:"Ubuntu",sans-serif;font-size:50px;font-weight:700;color:#fff}

/* about */
.about{top:659px;height:405px}
.about-emblem{position:absolute;left:74px;top:62px;width:242px;height:276px;display:flex;flex-direction:column;align-items:center;justify-content:center;gap:18px}
.about-emblem .sq{width:150px;height:150px;background:linear-gradient(135deg,#23b4dc,#3a55b0)}
.about-emblem span{font-family:"Ubuntu",sans-serif;font-size:30px;font-weight:500;color:var(--navy)}
.section-title{font-size:34px;font-weight:500;color:var(--navy)}
.about .section-title{position:absolute;left:434px;top:64px}
.body-copy{font-size:15px;line-height:27.6px;color:var(--text)}
.about .body-copy{position:absolute;left:434px;top:118px;width:700px}
.btn{position:absolute;height:46px;border-radius:23px;font-size:17px;font-weight:700;display:flex;align-items:center;justify-content:center;color:#fff;background:linear-gradient(180deg,#2a9fda,#3c55b0)}
.about .btn{left:434px;top:282px;width:180px}

/* doing */
.doing{top:1064px;height:457px;background:linear-gradient(180deg,#22bfe1 0%,#31c1e3 60%,#5ec9e6 80%,#2fb4dc 100%)}
.doing h2{position:absolute;top:50px;width:100%;text-align:center;font-size:34px;font-weight:500;color:#fff}
.card{position:absolute;top:128px;width:331px;height:264px;border-radius:24px;background:rgba(44,112,196,.62);color:#fff;text-align:center}
.card .icon{position:absolute;left:125px;top:22px;width:80px;height:80px;border-radius:50%;border:3px solid #fff;display:flex;align-items:center;justify-content:center}
.card h3{position:absolute;top:125px;width:100%;font-size:26px;font-weight:500}
.card p{position:absolute;top:164px;left:22px;right:22px;font-size:14.5px;line-height:24px}

/* solution */
.solution{top:1521px;height:444px}
.video{position:absolute;left:74px;top:52px;width:513px;height:339px;border-radius:28px;background:linear-gradient(135deg,#c5a560 0%,#d8d6d2 40%,#eceae6 70%,#a9b6c6 100%);overflow:hidden}
.play{position:absolute;left:223px;top:136px;width:66px;height:66px;border-radius:50%;background:rgba(255,255,255,.9)}
.solution .section-title{position:absolute;left:615px;top:56px}
.solution .body-copy{position:absolute;left:615px;top:110px;width:515px}
.solution .btn{left:615px;top:330px;width:180px}

/* support */
.support{top:1965px;height:363px;background:var(--navy)}
.support-photo{position:absolute;right:0;top:0;width:560px;height:363px;background:linear-gradient(90deg,var(--navy) 0%,#6a7cc0 35%,#d7dbe4 70%,#8d96a8 100%)}
.support h2{position:absolute;left:74px;top:42px;font-size:34px;font-weight:500;color:#fff}
.support .body-copy{position:absolute;left:74px;top:92px;width:650px;color:#fff}
.btn-light{position:absolute;left:74px;top:254px;width:180px;height:46px;border-radius:23px;background:#fff;color:var(--navy);font-size:17px;font-weight:700;display:flex;align-items:center;justify-content:center}

/* testimonials */
.testimonials{top:2328px;height:402px}
.testimonials h2{position:absolute;top:52px;width:100%;text-align:center;font-size:34px;font-weight:500;color:var(--navy)}
.quote{position:absolute;top:126px;width:330px;height:230px}
.quote p{font-size:15px;line-height:27.6px;color:var(--text)}
.person{position:absolute;top:128px;left:0;display:flex;align-items:center;gap:20px}
.avatar{width:90px;height:90px;border-radius:50%;background:radial-gradient(circle at 50% 40%,#e7e3df,#9fa4ab)}
.person strong{display:block;font-size:18px;font-weight:700;color:var(--sky);line-height:24px}
.person span{font-size:16px;color:var(--muted);line-height:22px}

/* footer */
.site-footer{top:2730px;height:290px;background:var(--navy);color:#fff}
.footer-brand{position:absolute;left:74px;top:70px;display:flex;align-items:center;gap:10px}
.footer-brand .brand-mark{background:#fff;width:30px;height:30px}
.footer-brand .brand-name{color:#fff;font-size:36px}
.copyright{position:absolute;left:74px;top:140px;font-size:13px;line-height:20px}
.socials{position:absolute;left:74px;top:208px;display:flex;gap:20px}
.socials i{width:22px;height:22px;border-radius:50%;background:#fff;display:block}
.fcol{position:absolute;top:54px}
.fcol h3{font-size:19px;font-weight:500;margin-bottom:4px}
.fcol li{list-style:none;font-size:14px;line-height:26.8px}
.news-item{font-size:14px;line-height:23px;width:240px;margin-bottom:14px}
.news-item em{display:block;font-style:normal;color:var(--cyan);font-weight:700;font-size:13px}
</style>
</head>
<body>

<header class="site-header">
  <div class="brand"><div class="brand-mark"></div><div class="brand-name">Tarvolen</div></div>
  <div class="brand-tag">Border Flow Reshaping Trade</div>
  <nav class="main-nav">
    <span class="active">Home</span><span>Products</span><span>Web App</span><span>About Us</span><span>Working at Tarvolen</span><span>News</span><span>Contact</span>
  </nav>
  <svg class="search" width="16" height="16" viewBox="0 0 16 16"><circle cx="6.5" cy="6.5" r="5" fill="none" stroke="#333" stroke-width="2"/><line x1="10.2" y1="10.2" x2="15" y2="15" stroke="#333" stroke-width="2.4"/></svg>
</header>

<section class="hero" role="img" aria-label="Glowing blue fibre-optic strands over a bright data surface">
  <h1>Tarvolen</h1>
  <div class="sub">Border Flow Reshaping Trade</div>
</section>

<section class="about">
  <div class="about-emblem"><div class="sq"></div><span>Tarvolen</span></div>
  <h2 class="section-title">About Tarvolen</h2>
  <p class="body-copy">Lorem ipsum dolor sit amet, consectetur adipiscing elit. Mauris mollis eleifend felis ac volutpat. Nunc sodales, augue a commodo consectetur, erat lorem semper ante, id vestibulum nunc odio eu felis. Aenean non erat at mi porttitor sagittis in et diam. Vestibulum a maximus turpis, quis euismod dolor. Class aptent taciti sociosqu ad litora torquent per conubia nostra, per inceptos himenaeos. Nullam mauris mauris, faucibus facilisis rutrum quis, egestas et nibh.</p>
  <div class="btn">READ MORE</div>
</section>

<section class="doing" role="img" aria-label="Earth seen from orbit with glowing city lights">
  <h2>What Tarvolen is Doing</h2>
  <div class="card" style="left:74px">
    <div class="icon"><svg width="42" height="36" viewBox="0 0 42 36"><rect x="2" y="2" width="34" height="26" rx="3" fill="none" stroke="#fff" stroke-width="3"/><line x1="2" y1="9" x2="36" y2="9" stroke="#fff" stroke-width="3"/><circle cx="32" cy="27" r="7" fill="#fff"/></svg></div>
    <h3>Web Application</h3>
    <p>Class aptent taciti sociosqu ad litora torquent per conubia nostra ex vitae nulla suscipit porttitor..</p>
  </div>
  <div class="card" style="left:435px">
    <div class="icon"><svg width="36" height="42" viewBox="0 0 36 42"><path d="M8 40V30C3 27 1 21 2 15 4 6 12 1 20 2c8 1 14 8 14 16 0 4-2 6-4 8v6h-6v8z" fill="#fff"/></svg></div>
    <h3>Artificial Intelligence</h3>
    <p>Class aptent taciti sociosqu ad litora torquent per conubia nostra ex vitae nulla suscipit porttitor..</p>
  </div>
  <div class="card" style="left:795px">
    <div class="icon"><svg width="40" height="40" viewBox="0 0 40 40"><rect x="6" y="32" width="16" height="5" fill="#fff"/><path d="M14 32 L10 14 L26 8" fill="none" stroke="#fff" stroke-width="4"/><circle cx="10" cy="14" r="4" fill="#fff"/><path d="M26 4 l8 4 -8 4" fill="none" stroke="#fff" stroke-width="3"/></svg></div>
    <h3>Robotic Process</h3>
    <p>Class aptent taciti sociosqu ad litora torquent per conubia nostra ex vitae nulla suscipit porttitor..</p>
  </div>
</section>

<section class="solution">
  <div class="video" role="img" aria-label="Team gathered around a monitor in a bright office with sticky notes on the wall">
    <div class="play"><svg width="66" height="66" viewBox="0 0 66 66"><path d="M26 19 L48 33 26 47z" fill="#444"/></svg></div>
  </div>
  <h2 class="section-title">Tarvolen Solution</h2>
  <p class="body-copy">Lorem ipsum dolor sit amet, consectetur adipiscing elit mollis eleifend felis ac volutpat. Nunc sodales, augue a commodo consectetur, erat lorem semper ante, id vestibulum nunc odio eu felis. Aenean non erat at mi porttitor sagittis in et diam. Vestibulum a maximus turpis, quis euismod dolor. Class aptent taciti sociosqu ad litora torquent per conubia nostra, per inceptos himenaeos. Nullam mauris mauris, faucibus facilisis rutrum quis, egestas et nibh.</p>
  <div class="btn">WATCH VIDEO</div>
</section>

<section class="support">
  <div class="support-photo" role="img" aria-label="Support agent with headset working at a computer"></div>
  <h2>Customer Support</h2>
  <p class="body-copy">Lorem ipsum dolor sit amet, consectetur adipiscing elit mollis eleifend felis ac volutpat.<br>Nunc sodales, augue a commodo consectetur, erat lorem semper ante, id vestibulum nunc odio eu felis. Aenean non erat at mi&nbsp; porttitor sagittis in et diam. Vestibulum a maximus turpis, quis euismod dolor. Class aptent taciti sociosqu ad litora torquent per conubia nostra,<br>per inceptos himenaeos.</p>
  <div class="btn-light">CONTACT US</div>
</section>

<section class="testimonials">
  <h2>Testimonials</h2>
  <div class="quote" style="left:74px">
    <p>“&nbsp; Class aptent taciti sociosqu ad litora torquent per conubia nostra, per inceptos himenaeos. Nullam mauris mauris, faucibus facilisis rutrum quis, egestas et nibh. ..</p>
    <div class="person"><div class="avatar" role="img" aria-label="Client portrait"></div><div><strong>Name Heading</strong><span>Company</span></div></div>
  </div>
  <div class="quote" style="left:435px">
    <p>“&nbsp; Class aptent taciti sociosqu ad litora torquent per conubia nostra, per inceptos himenaeos. Nullam mauris mauris, faucibus facilisis rutrum quis, egestas et nibh. ..</p>
    <div class="person"><div class="avatar" role="img" aria-label="Client portrait"></div><div><strong>Name Heading</strong><span>Company</span></div></div>
  </div>
  <div class="quote" style="left:794px">
    <p>“&nbsp; Class aptent taciti sociosqu ad litora torquent per conubia nostra, per inceptos himenaeos. Nullam mauris mauris, faucibus facilisis rutrum quis, egestas et nibh. ..</p>
    <div class="person"><div class="avatar" role="img" aria-label="Client portrait"></div><div><strong>Name Heading</strong><span>Company</span></div></div>
  </div>
</section>

<footer class="site-footer">
  <div class="footer-brand"><div class="brand-mark"></div><div class="brand-name">Tarvolen</div></div>
  <div class="copyright">Copyright © 2019 Company Name<br>All Rights Reserved</div>
  <div class="socials"><i></i><i></i><i></i><i></i><i></i></div>
  <div class="fcol" style="left:363px"><h3>Site Map</h3><ul><li>Home</li><li>Products</li><li>Web app</li><li>About us</li><li>Working at Tarvolen</li><li>News</li><li>Contact us</li></ul></div>
  <div class="fcol" style="left:615px"><h3>Products</h3><ul><li>Class aptent taciti</li><li>Sociosqu ad litora</li><li>Torquent per</li><li>Conubia nostra</li><li>Per inceptos himenaeos.</li></ul></div>
  <div class="fcol" style="left:875px"><h3>News</h3>
    <div class="news-item">Class aptent taciti sociosqu ad litora torquent per conubia..<em>Jun 29, 2019</em></div>
    <div class="news-item">Class aptent taciti sociosqu ad litora torquent per conubia..<em>Jun 29, 2019</em></div>
  </div>
</footer>

</body>
</html>
```